Veltrano.co - Polar Expeditions Specialists

We need a modern, visually striking business card for Veltrano.co, a company specialized in selling expedition cruises to the most remote regions on Earth, with a focus on the Arctic and Antarctica. The design should instantly communicate that the cardholder is an expert in polar travel. Use clean, premium aesthetics with cool tones like icy blue and white, possibly incorporating polar imagery (ice, glaciers, penguins, etc.)

Attached the logo

Contact Information for Business Card

Feels high-end and trustworthy.. Visually memorable — encourages people to keep it

Colors
0054AA
0677BA
7BADD7
CADEEF
E8F1F8

Requirements
Must have
• ice, glaciers, penguins, montains
Nice to have
• modern, transparente,

```html
<!DOCTYPE html>
<html lang="en">
<head>
<meta charset="utf-8">
<title>Veltrano.co Business Card</title>
<link href="https://fonts.googleapis.com/css2?family=Poppins:wght@300;400;600;700&display=swap" rel="stylesheet">
<style>
  :root {
    --stage: #333436;
    --brand-blue: #3576b8;
    --deep-blue: #1f3a78;
    --ice-blue: #8fb9e0;
    --paper: #ffffff;
    --ink-grey: #6a6a6a;
  }
  html, body {
    margin: 0;
    padding: 0;
    width: 1200px;
    height: 689px;
    overflow: hidden;
    background: var(--stage);
    font-family: "Poppins", sans-serif;
  }
  .canvas {
    position: relative;
    width: 1200px;
    height: 689px;
  }
  .card {
    position: absolute;
    top: 190px;
    width: 540px;
    height: 309px;
    border-radius: 4px;
    overflow: hidden;
    box-shadow: 0 14px 30px rgba(0,0,0,.45);
  }
  /* Front side */
  .card-front {
    left: 40px;
    background: var(--brand-blue);
  }
  .front-art {
    position: absolute;
    left: 0;
    bottom: 0;
    width: 360px;
    height: 250px;
    border-top-right-radius: 180px 250px;
    background: linear-gradient(100deg, var(--deep-blue) 0%, #2c5293 40%, #5f86b8 75%, var(--ice-blue) 100%);
  }
  .front-brand {
    position: absolute;
    right: 34px;
    top: 104px;
    color: var(--paper);
    text-align: left;
  }
  .brand-name {
    margin: 0;
    font-weight: 700;
    font-size: 46px;
    line-height: 1;
    letter-spacing: .5px;
  }
  .brand-tagline {
    margin: 6px 0 0 4px;
    font-weight: 600;
    font-size: 11.5px;
    letter-spacing: .3px;
  }
  /* Back side */
  .card-back {
    left: 620px;
    background: var(--paper);
  }
  .back-brand {
    position: absolute;
    left: 60px;
    top: 52px;
    color: var(--brand-blue);
    display: flex;
    align-items: center;
    gap: 14px;
  }
  .brand-dot {
    width: 18px;
    height: 18px;
    border-radius: 50%;
    background: var(--brand-blue);
    flex: none;
  }
  .back-brand .brand-name { font-size: 42px; }
  .back-brand .brand-tagline { font-size: 11px; }
  .holder {
    position: absolute;
    left: 60px;
    top: 196px;
    width: 200px;
  }
  .holder-name {
    margin: 0;
    color: var(--brand-blue);
    font-weight: 700;
    font-size: 20px;
    letter-spacing: .5px;
  }
  .holder-role {
    margin: 2px 0 0;
    color: var(--ink-grey);
    font-weight: 400;
    font-size: 13px;
  }
  .divider {
    position: absolute;
    left: 270px;
    top: 184px;
    width: 1.5px;
    height: 78px;
    background: var(--brand-blue);
  }
  .contact-list {
    position: absolute;
    left: 290px;
    top: 184px;
    margin: 0;
    padding: 0;
    list-style: none;
    color: var(--ink-grey);
    font-weight: 300;
    font-size: 13px;
  }
  .contact-list li {
    display: flex;
    align-items: center;
    gap: 8px;
    height: 26px;
  }
  .contact-list svg {
    width: 12px;
    height: 12px;
    fill: var(--brand-blue);
    flex: none;
  }
</style>
</head>
<body>
<main class="canvas">
  <section class="card card-front">
    <div class="front-art" role="img" aria-label="Illustration of a polar bear with penguins on ice"></div>
    <div class="front-brand">
      <p class="brand-name">Veltrano.co</p>
      <p class="brand-tagline">Polar Expeditions Specialists</p>
    </div>
  </section>

  <section class="card card-back">
    <div class="back-brand">
      <span class="brand-dot"></span>
      <div>
        <p class="brand-name">Veltrano.co</p>
        <p class="brand-tagline">Polar Expeditions Specialists</p>
      </div>
    </div>

    <div class="holder">
      <p class="holder-name">MARCUS REDFIELD</p>
      <p class="holder-role">President</p>
    </div>

    <div class="divider"></div>

    <ul class="contact-list">
      <li>
        <svg viewBox="0 0 24 24" aria-hidden="true"><path d="M6.6 10.8a15 15 0 0 0 6.6 6.6l2.2-2.2a1 1 0 0 1 1-.25 11.4 11.4 0 0 0 3.6.57 1 1 0 0 1 1 1V20a1 1 0 0 1-1 1A17 17 0 0 1 3 4a1 1 0 0 1 1-1h3.5a1 1 0 0 1 1 1c0 1.25.2 2.45.57 3.57a1 1 0 0 1-.25 1z"/></svg>
        555-310-4827
      </li>
      <li>
        <svg viewBox="0 0 24 24" aria-hidden="true"><path d="M2 5h20v14H2zm2 2v.5l8 5 8-5V7l-8 5z"/></svg>
        marcusredfield@veltrano.co
      </li>
      <li>
        <svg viewBox="0 0 24 24" aria-hidden="true"><path d="M12 2a10 10 0 1 0 0 20 10 10 0 0 0 0-20zm6.9 6h-3a15 15 0 0 0-1.3-3.9A8 8 0 0 1 18.9 8zM12 4c.8 1.2 1.5 2.5 1.9 4h-3.8c.4-1.5 1.1-2.8 1.9-4zM4.3 14a8 8 0 0 1 0-4h3.4a16 16 0 0 0 0 4zm.8 2h3a15 15 0 0 0 1.3 3.9A8 8 0 0 1 5.1 16zm3-8h-3a8 8 0 0 1 4.3-3.9A15 15 0 0 0 8.1 8zM12 20c-.8-1.2-1.5-2.5-1.9-4h3.8c-.4 1.5-1.1 2.8-1.9 4zm2.3-6H9.7a14 14 0 0 1 0-4h4.6a14 14 0 0 1 0 4zm.3 5.9a15 15 0 0 0 1.3-3.9h3a8 8 0 0 1-4.3 3.9zm1.7-5.9a16 16 0 0 0 0-4h3.4a8 8 0 0 1 0 4z"/></svg>
        www.veltrano.co
      </li>
    </ul>
  </section>
</main>
</body>
</html>
```